Velmarsh Group Webpage Design

We need a new website for our company. The company is Velmarsh Group Pty Ltd. We are in the business of Asbestos Removal; Demolition; Earthworks and Transport. We do not advertise and would like our website to be a reference point for our clients / potential clients and also to make our services known to those searching the internet for the services we offer. Some examples of the style of website we are after are:
http://www.quarnedemolition-example.com.au/
http://m.brintowerdemolitions-example.com.au/
http://www.fenwarddemolition-example.com.au
http://www.tolvik-example.com.au
http://www.ptrservices-example.com.au
http://www.steadfast-dismantling-example.com.au
We will need to work on content. Enclosed is an example. We also need to purchase the domain velmarshgroup-example.com.au and need to set up email accounts and ensure the website is mobile friendly. We have a company logo and have built our business on delivering professional, quality services on time. We would like the webpage to be simple, informative and professional - black and white / grey themed. We would also like to add a photo gallery etc later.

Industry/Entity Type

Construction

Coding

Coded - Design and coding required

Number of Pages Required

1 page

Colors
000000
fcfcfc
959595
dddddd

Requirements
Must have
• Information regarding the services we provide

```html
<!DOCTYPE html>
<html lang="en">
<head>
<meta charset="utf-8">
<title>Velmarsh Group</title>
<link href="https://fonts.googleapis.com/css2?family=Open+Sans:ital,wght@0,400;0,600;0,700;1,400&display=swap" rel="stylesheet">
<style>
:root{
  --black:#000000;
  --ink:#231f20;
  --text:#333333;
  --muted:#777777;
  --grey:#959595;
  --line:#dddddd;
  --paper:#fcfcfc;
  --panel:#f1f1f1;
  --bar-top:#6a6a6a;
  --bar-bottom:#3a3a3a;
}
*{margin:0;padding:0;box-sizing:border-box}
html,body{width:938px;height:1200px;overflow:hidden}
body{font-family:'Open Sans',sans-serif;background:var(--paper);color:var(--text);position:relative}
.abs{position:absolute}
/* header */
.header-band{left:0;top:0;width:938px;height:91px;background:#fff}
.brand-block{left:77px;top:0;width:270px;height:91px}
.brand-name{left:101px;top:30px;color:#fff;font-size:20px;font-weight:400;letter-spacing:3px;line-height:1.2}
.brand-sub{left:101px;top:53px;width:210px;color:#fff;font-size:7px;letter-spacing:6px;text-align:center;border-top:1px solid #fff;padding-top:1px}
.topbar{left:330px;top:0;width:531px;height:58px;background:linear-gradient(90deg,#fff,#ececec)}
.contact-item{top:14px;display:flex;align-items:center;gap:10px}
.contact-icon{width:30px;height:30px;background:var(--ink);border-radius:3px;display:flex;align-items:center;justify-content:center}
.contact-label{font-size:8px;color:#555}
.contact-value{font-size:11.5px;font-weight:600;color:#444}
.nav{left:337px;top:58px;width:524px;height:33px;background:linear-gradient(var(--bar-top),var(--bar-bottom));display:flex;justify-content:space-around;align-items:center;padding-left:14px}
.nav a{color:#fff;text-decoration:none;font-size:10px;font-weight:600}
/* hero */
.hero{left:77px;top:91px;width:784px;height:293px;background:linear-gradient(160deg,#6b6257 0%,#8a7d6a 35%,#a59779 55%,#5a534a 80%,#3f3b36 100%)}
.hero-caption{left:77px;top:220px;width:356px;height:104px}
.hero-title{left:101px;top:236px;color:#fff;font-size:19px;font-weight:700}
.hero-sub{left:103px;top:267px;color:#fff;font-size:12.5px;font-weight:600;letter-spacing:.3px}
.hero-note{left:104px;top:289px;color:#fff;font-size:11px}
/* services */
.section-title{font-size:12.5px;font-weight:700;color:var(--ink)}
.services-intro{left:158px;top:407px;width:420px;font-size:9px;line-height:17px;color:#666}
.arrow-btn{width:16px;height:16px;border:1px solid #ccc;border-radius:3px;background:#fff;display:flex;align-items:center;justify-content:center}
.card{top:462px;width:168px}
.card-photo{height:93px}
.card-label{height:27px;background:linear-gradient(#777,#444);color:#fff;font-size:10px;font-weight:600;padding:7px 11px}
.card-text{margin-top:7px;font-size:8.5px;line-height:17.5px;color:#666;padding-left:1px}
.safety{left:77px;top:668px;width:545px;height:65px;border:1px solid #ccc;background:#fff}
.safety-text{left:93px;top:683px;width:410px;font-size:8.5px;line-height:17.5px;color:#666}
.btn{background:linear-gradient(#666,#333);color:#fff;font-weight:700;border-radius:2px;display:flex;align-items:center;justify-content:center;box-shadow:0 1px 2px rgba(0,0,0,.3)}
/* about */
.about-photo{left:78px;top:788px;width:200px;height:138px;background:linear-gradient(135deg,#3c4650,#6a5a4a 50%,#c0612e 70%,#3a3f45)}
.about-text{left:305px;top:783px;width:316px;font-size:8.5px;line-height:17.5px;color:#666}
/* right column */
.quick{left:649px;top:402px;width:212px;height:316px;background:var(--panel);border:1px solid var(--line)}
.quick-title{left:663px;top:419px;font-size:12.5px;font-weight:700;color:var(--ink)}
.quick-note{left:663px;top:441px;width:180px;font-size:8px;line-height:17px;color:#666}
.field{left:663px;width:184px;height:25px;background:#fff;border:1px solid #ccc;border-radius:2px;font-size:8.5px;color:#666;padding:6px 10px}
.quote{left:649px;top:770px;width:212px;height:93px;background:#f0f0f0;border:1px solid var(--line)}
.quote-text{left:678px;top:791px;width:170px;font-size:8.5px;font-style:italic;line-height:17.5px;color:#666}
.avatar{left:652px;top:874px;width:41px;height:41px;border-radius:50%;background:linear-gradient(#ddd,#999)}
/* footer */
.footer{left:0;top:972px;width:938px;height:180px;background:#f2f2f2;border-top:1px solid #e6e6e6;border-bottom:1px solid #e6e6e6}
.foot-brand{left:77px;top:1050px;color:var(--ink);font-size:18px;font-weight:400;letter-spacing:3px}
.foot-brand-sub{left:77px;top:1071px;width:168px;font-size:6px;letter-spacing:6px;text-align:center;border-top:1px solid var(--ink);color:var(--ink)}
.foot-col{top:1003px}
.foot-col h4{font-size:10.5px;font-weight:700;color:var(--ink);margin-bottom:9px}
.foot-col li{list-style:none;font-size:8.5px;color:#666;line-height:20px}
.social{left:722px;top:1087px;display:flex;gap:7px}
.social span{width:22px;height:22px;border-radius:50%;background:#888}
.copyright{left:0;top:1170px;width:938px;text-align:center;font-size:8.5px;color:#666;padding-right:18px}
</style>
</head>
<body>

<div class="abs header-band"></div>
<svg class="abs brand-block" viewBox="0 0 270 91" width="270" height="91"><polygon points="0,0 250,0 270,91 0,91" fill="#231f20"/></svg>
<div class="abs brand-name">VELMARSH</div>
<div class="abs brand-sub">GROUP</div>

<div class="abs topbar"></div>
<div class="abs contact-item" style="left:497px">
  <div class="contact-icon"><svg width="14" height="14" viewBox="0 0 24 24"><path fill="#fff" d="M6.6 10.8a15 15 0 0 0 6.6 6.6l2.2-2.2a1 1 0 0 1 1-.25 11.4 11.4 0 0 0 3.6.57 1 1 0 0 1 1 1V20a1 1 0 0 1-1 1A17 17 0 0 1 3 4a1 1 0 0 1 1-1h3.5a1 1 0 0 1 1 1c0 1.25.2 2.45.57 3.57a1 1 0 0 1-.25 1z"/></svg></div>
  <div><div class="contact-label">CALL US :</div><div class="contact-value">0412 555 730</div></div>
</div>
<div class="abs contact-item" style="left:652px">
  <div class="contact-icon"><svg width="13" height="10" viewBox="0 0 26 20"><rect x="0" y="4" width="26" height="16" rx="1" fill="#fff"/><path d="M0 4 L13 13 L26 4" stroke="#231f20" stroke-width="2" fill="none"/></svg></div>
  <div><div class="contact-label">EMAIL US :</div><div class="contact-value">vgdemolition@example.com</div></div>
</div>

<nav class="abs nav"><a href="#">HOME</a><a href="#">ABOUT US</a><a href="#">SERVICES</a><a href="#">HOURS OF OPERATION</a><a href="#">CONTACT US</a></nav>

<div class="abs hero" role="img" aria-label="Excavator, bulldozer and dump truck working on a dusty earthmoving site"></div>
<svg class="abs hero-caption" viewBox="0 0 356 104" width="356" height="104"><polygon points="0,0 330,0 356,104 0,104" fill="rgba(20,20,20,.72)"/></svg>
<div class="abs hero-title">VELMARSH</div>
<div class="abs hero-sub">TRANSPORT &nbsp;.&nbsp; DEMOLITION &nbsp;.&nbsp; EARTHMOVING</div>
<div class="abs hero-note">WAS ESTABLISHED BY DIRECTOR MARCUS VELMARSH</div>

<div class="abs section-title" style="left:76px;top:414px">SERVICES</div>
<p class="abs services-intro">Velmarsh Transport and Demolition offer an extensive range of services including Demolition, Earthworks and Asbestos Removal.</p>
<div class="abs arrow-btn" style="left:584px;top:416px"><svg width="6" height="8"><path d="M5 1 L1 4 L5 7" stroke="#999" fill="none"/></svg></div>
<div class="abs arrow-btn" style="left:605px;top:416px"><svg width="6" height="8"><path d="M1 1 L5 4 L1 7" stroke="#999" fill="none"/></svg></div>

<div class="abs card" style="left:77px">
  <div class="card-photo" role="img" aria-label="Orange excavator demolishing a building" style="background:linear-gradient(135deg,#b8b2a8,#8f877c 55%,#d0552a 80%,#6d6a63)"></div>
  <div class="card-label">DEMOLITION</div>
  <p class="card-text">Velmarsh Transport and Demolition provide an extensive range of demolition services.</p>
</div>
<div class="abs card" style="left:266px">
  <div class="card-photo" role="img" aria-label="Wheel loader working on earthworks at sunset" style="background:linear-gradient(160deg,#9aa6b0,#6d6252 50%,#4a3f33)"></div>
  <div class="card-label">EARTHWORKS</div>
  <p class="card-text">Velmarsh Transport and Demolition possess all necessary equipment and skilled personnel to provide...</p>
</div>
<div class="abs card" style="left:454px">
  <div class="card-photo" role="img" aria-label="Stack of corrugated asbestos roofing sheets" style="background:linear-gradient(135deg,#8a8a86,#4e4e4b 50%,#a3a39e)"></div>
  <div class="card-label">ASBESTOS</div>
  <p class="card-text">Asbestos is a naturally occurring silicate mineral made up of tiny fibres. When disturbed...</p>
</div>

<div class="abs safety"></div>
<p class="abs safety-text">The safety of our clients, workforce and wider community is of paramount importance to Velmarsh Transport and Demolition. We employ a comprehensive Safety Management System ensuring.</p>
<div class="abs btn" style="left:511px;top:687px;width:98px;height:28px;font-size:9px">CONTACT HERE</div>

<div class="abs section-title" style="left:78px;top:757px">ABOUT VELMARSH GROUP</div>
<div class="abs about-photo" role="img" aria-label="Worker in hard hat and high-visibility jacket beside a locomotive"></div>
<p class="abs about-text">Velmarsh Transport Pty Ltd was established by Director Marcus Velmarsh in 2002 with a focus providing services within the transport industry. Over time the company has developed and expanded to include the provision of Earthworks and Demolition. Marcus has over 10 years' experience working at all levels within these industries focusing primarily on Demolition and Earthworks in recent times.</p>
<div class="abs btn" style="left:304px;top:898px;width:90px;height:25px;font-size:8px">READ MORE</div>

<div class="abs quick"></div>
<div class="abs quick-title">QUICK CONTACT</div>
<p class="abs quick-note">MAKE SURE YOU'RE DEALING WITH A LICENSED PROFESSIONAL</p>
<div class="abs field" style="top:481px">Name</div>
<div class="abs field" style="top:516px">Email</div>
<div class="abs field" style="top:550px">Phone</div>
<div class="abs field" style="top:585px">Subject</div>
<div class="abs field" style="top:619px;height:51px">MEssage</div>
<div class="abs btn" style="left:663px;top:679px;width:184px;height:28px;font-size:10px">SUBMIT NOW</div>

<div class="abs section-title" style="left:649px;top:738px">TESTIMONIALS</div>
<svg class="abs" style="left:843px;top:742px" width="16" height="8"><path d="M4 1 L1 4 L4 7 M12 1 L15 4 L12 7" stroke="#aaa" fill="none"/></svg>
<div class="abs quote"></div>
<svg class="abs" style="left:781px;top:862px" width="24" height="15"><polygon points="0,0 24,0 2,14" fill="#f0f0f0"/><path d="M2 0 L2 14 L24 0" stroke="#ddd" fill="none"/></svg>
<div class="abs" style="left:664px;top:782px;font-size:20px;color:#aaa;font-style:italic">“</div>
<p class="abs quote-text">Lorem Ipsum is simply dummy text of the printing and typesetting industry. Lorem Ipsum has been the industry...</p>
<div class="abs" style="left:837px;top:826px;font-size:20px;color:#aaa;font-style:italic">”</div>
<div class="abs avatar" role="img" aria-label="Portrait of the client giving the testimonial"></div>
<div class="abs" style="left:704px;top:886px;font-size:8.5px;font-weight:700;color:var(--ink)">CONNOR ASHBY</div>
<div class="abs" style="left:704px;top:900px;font-size:8.5px;font-style:italic;color:#666">Business man</div>

<footer class="abs footer"></footer>
<div class="abs foot-brand">VELMARSH</div>
<div class="abs foot-brand-sub">GROUP</div>
<div class="abs foot-col" style="left:302px"><h4>WELCOME</h4><ul><li>Home</li><li>About Us</li><li>Services</li><li>Hours of Operation</li><li>Contact us</li></ul></div>
<div class="abs foot-col" style="left:433px"><h4>SERVICES</h4><ul><li>Demolition</li><li>Earthworks</li><li>Asbestos</li><li>Hours of Operation</li></ul></div>
<div class="abs foot-col" style="left:560px"><h4>HOURS OF OPERATION</h4><ul><li>Safety</li><li>Environment</li></ul></div>
<div class="abs foot-col" style="left:721px"><h4>INFORMATION</h4><ul><li>Terms &amp; Conditions</li><li>Privacy Policy</li><li>Disclaimer</li></ul></div>
<div class="abs social"><span></span><span></span><span></span><span></span><span></span></div>
<div class="abs copyright">Copyrights. 2015. Velmarsh. All rights reserved.</div>

</body>
</html>
```